Schlichtes Design für Malerbetrieb
Zielgruppe
Wir sind ein mittelgroßer Malerbetrieb in München mit umfangreichem Leistungsspektrum.
Unsere Hauptleistungen sind: Fassadenrenovierung, Altbausanierung, Betoninstandsetzung, Balkonabdichtung (kein Neubau!).
Unsere Zielgruppen sind: Hausverwaltungen, Firmen und Privatpersonen.
Unsere Kunden schätzen: Konstruktive Organisation und Planung im Vorfeld, Zuverlässigkeit, saubere Arbeitsweise, dauerhafte Balkonabdichtungen.
Aufgabenstellung
Wir möchten eine langlebige, stilvolle, minimalistische Homepage.
Wir möchten von der bestehenden Homepage nur die Schriftart für unseren Firmennamen (Century Gothic) und wenn möglich (nicht zwingend), irgendwo das florale Muster einbauen. Corporate-Design haben wir nicht.
Farbtöne: Firmennamen Orange (hellorange bis erdiges Orange möglich, da sind wir nicht fixiert) , einen dunklen Hintergrundfarbton (Petrol-Blaugrau ?) mit gelbem (neon bis senfgelb) Akzent (Linien), Blumenmuster weiß, grau.
Dies sind nur unsere Ideen. Wir sind aber auch absolut offen für eure Profi-Ideen.
Wir möchten uns von den unzähligen langweiligen 'Pinselseiten mit veralteten Bilder' unserer Kollegen interessant und mit Stil abheben.
Eher nach dem Motto 'weniger ist mehr'.
Einen positiven, sympathischen Eindruck geben und unsere Leistungen in den Vordergrund bringen.
Da wir viele Stammkunden haben, betreiben wir kein Social-Media und möchten dies vorerst auch nicht tun.
Die Seite wird in den nächsten Jahren nicht verändert, höchstens die Bilder aktualisiert.
Die Texte haben wir alle selbst entworfen und möchten wir so übernehmen.
Die Galerien sollen unkompliziert anzuschauen sein.
Uns gefällt die Struktur und Schlichtheit von https://vaartmolen.nl/ oder Timbra.de gut und wir mögen Vintage-Grafiken gerne.
Einerseits darf die Seite geradlinig, andererseits aber auch rund und floral wirken.

```html
<!DOCTYPE html>
<html lang="de">
<head>
<meta charset="utf-8">
<title>Kolbrit Malerarbeiten – Webdesign</title>
<link href="https://fonts.googleapis.com/css2?family=Open+Sans:wght@400;600;700&family=Noto+Serif:wght@400&family=Roboto:wght@400&display=swap" rel="stylesheet">
<style>
  :root{
    --orange:#e2720f;
    --slate:#4c5a63;
    --ink:#3b464d;
    --paper:#ffffff;
    --mist-top:#a7b3bb;
    --mist-bottom:#dfe3e6;
    --steel-top:#86929a;
    --steel-bottom:#5d6a72;
    --footer:#4a5055;
    --footbar:#2f3439;
    --stage:#d9d9d9;
    --lightbox:#1f2428;
    --white:#ffffff;
  }
  *{margin:0;padding:0;box-sizing:border-box}
  html,body{width:1200px;height:3892px;overflow:hidden}
  body{position:relative;background:var(--paper);font-family:"Open Sans",sans-serif;color:var(--ink)}
  .abs{position:absolute}

  /* brand: plain square + name in text font */
  .brand-square{background:var(--slate)}
  .brand-name{font-family:"Open Sans",sans-serif;font-weight:600;color:var(--slate);line-height:1;white-space:nowrap}

  /* site */
  .site{left:0;top:544px;width:1200px;height:2349px;overflow:hidden}
  .site-shadow{left:0;top:536px;width:1200px;height:10px;background:linear-gradient(#fff,#6b6b6b)}
  .site-header{left:0;top:0;width:1200px;height:136px;background:linear-gradient(90deg,#e9e9e8,#f6f6f5 60%,#eeeeed)}
  .nav{right:145px;top:93px;display:flex;gap:31px;font-size:15px;color:#3a3a3a;text-transform:uppercase;letter-spacing:.01em}
  .hero-photo{left:0;top:136px;width:1200px;height:650px;background:linear-gradient(160deg,#3b3430 0%,#8a7a66 45%,#c9b79d 65%,#5d534a 100%)}
  .hero-title{left:0;top:380px;width:1200px;text-align:center;font-family:"Noto Serif",serif;font-size:42px;color:var(--white)}
  .hero-sub{left:0;top:436px;width:1200px;text-align:center;font-family:"Roboto",sans-serif;font-size:27px;line-height:34px;color:var(--white)}
  .serif-heading{font-family:"Noto Serif",serif;color:var(--white);font-size:29px;letter-spacing:.02em;font-weight:400}
  .copy{font-size:13px;line-height:21px}
  .copy p{margin-bottom:21px}
  .copy strong{font-weight:700}
  .gallery{left:632px;top:1570px;width:452px;height:530px;display:grid;grid-template-columns:repeat(3,1fr);grid-template-rows:repeat(5,1fr);gap:1px}
  .tile{position:relative}
  .tile-wide{grid-column:1/3;grid-row:1/3}
  .footer{left:0;top:2161px;width:1200px;height:148px;background:var(--footer);color:#e7e9ea;font-size:14px;line-height:21px}
  .footbar{left:0;top:2309px;width:1200px;height:40px;background:var(--footbar);color:#dcdfe1;font-size:14px}

  /* lightbox */
  .stage{left:0;top:2893px;width:1200px;height:999px;background:linear-gradient(#c9c9c9,var(--stage) 30%,#ececec)}
  .lightbox{left:65px;top:3045px;width:1068px;height:665px;background:var(--lightbox);overflow:hidden}
  .lb-caption{left:73px;top:600px;font-size:12px;line-height:19px;color:#e1e3e4}
</style>
</head>
<body>

<!-- Brand -->
<div class="abs brand-square" style="left:262px;top:236px;width:64px;height:64px"></div>
<div class="abs brand-name" style="left:350px;top:241px;font-size:48px">Kolbrit Malerarbeiten</div>

<div class="abs site-shadow"></div>

<!-- Website -->
<div class="abs site">
  <header class="abs site-header">
    <div class="abs brand-square" style="left:74px;top:52px;width:32px;height:32px"></div>
    <div class="abs brand-name" style="left:118px;top:54px;font-size:24px">Kolbrit Malerarbeiten</div>
    <nav class="abs nav"><span>Home</span><span>Leistungen</span><span>Portrait</span><span>Ausbildung</span><span>Kontakt</span></nav>
  </header>

  <div class="abs hero-photo" role="img" aria-label="Foto: renovierter Modeladen mit Regalen, Tischen und Rundbogenfenstern"></div>

  <svg class="abs" style="left:0;top:672px" width="1200" height="1500" viewBox="0 0 1200 1500">
    <defs>
      <linearGradient id="mist" x1="0" y1="0" x2="0.3" y2="1">
        <stop offset="0" stop-color="#a7b3bb"/>
        <stop offset="1" stop-color="#dfe3e6"/>
      </linearGradient>
      <linearGradient id="steel" x1="0" y1="0" x2="0" y2="1">
        <stop offset="0" stop-color="#86929a"/>
        <stop offset="1" stop-color="#5d6a72"/>
      </linearGradient>
    </defs>
    <polygon points="0,0 802,106 1200,0 1200,800 0,800" fill="url(#mist)"/>
    <polygon points="0,749 710,816 1200,749 1200,1489 0,1489" fill="url(#steel)"/>
  </svg>

  <div class="abs hero-title">Lorem ipsum dolor sit amet</div>
  <div class="abs hero-sub">Consetetur sadipscing elitr,<br>sed diam nonumy eirmod temporamet.</div>
  <svg class="abs" style="left:36px;top:505px" width="22" height="34"><polyline points="18,3 4,17 18,31" fill="none" stroke="#fff" stroke-width="2"/></svg>
  <svg class="abs" style="left:1142px;top:505px" width="22" height="34"><polyline points="4,3 18,17 4,31" fill="none" stroke="#fff" stroke-width="2"/></svg>

  <h2 class="abs serif-heading" style="left:0;width:1200px;text-align:center;top:909px">MALERARBEITEN</h2>
  <svg class="abs" style="left:145px;top:970px" width="907" height="20"><line x1="0" y1="10" x2="440" y2="10" stroke="#fff" stroke-width="1"/><line x1="467" y1="10" x2="907" y2="10" stroke="#fff" stroke-width="1"/><circle cx="453" cy="10" r="4" fill="none" stroke="#fff"/></svg>

  <div class="abs copy" style="left:145px;top:1041px;width:430px">
    <p>Flächen, die einheitlich und streifenlos erscheinen, erfreuen den Betrachter. Sie unterstützen primär die optische Erscheinung eines Objekts.</p>
    <p>Auf längere Zeit gesehen leisten Anstriche jedoch weitere wesentliche Dienste. Sie schützen Ihr Gebäude oder Ihre Wohnung vor Witterungseinflüssen, mechanischer Beschädigung und dem Nagen der Zeit.</p>
    <p><strong>Unsere Tätigkeit und unser Fachwissen schützen Ihren Besitz.</strong></p>
  </div>
  <div class="abs copy" style="left:632px;top:1041px;width:425px">
    <p>Bei der Erstellung von baulichen Schutzmaßnahmen müssen alle Objektgegebenheiten mit einbezogen werden. Um einen dauerhaften Bestand von Objekten zu gewährleisten, muss jeder Beteiligte über das eigene Aufgabengebiet hinweg denken.</p>
    <p>Wir betrachten bei der Ausarbeitung unserer Leistungen jedes Bauteil gesondert mit seinen Eigenschaften. Die stets erneuerten Technologien von Anstrichmitteln in Bezug auf Oberflächenbeschaffenheit, Umweltverträglichkeit und Beständigkeit setzen wir jederzeit optimal ein.</p>
    <p><strong>Nur Fachleute suchen nach Ursachen und erarbeiten die richtigen Lösungen.</strong></p>
  </div>

  <h2 class="abs serif-heading" style="left:145px;top:1562px">IMPRESSIONEN</h2>
  <div class="abs copy" style="left:145px;top:1630px;width:390px;color:#f2f4f5">
    <p>Lorem ipsum dolor sit amet, consetetur sadipscing elitr, sed diam nonumy eirmod tempor invidunt ut labore et dolore magna aliquyam erat, sed diam voluptua.</p>
    <p>At vero eos et accusam et justo duo dolores et ea rebum. Stet clita kasd gubergren, no sea takimata sanctus est Lorem ipsum dolor sit amet.</p>
    <p>Lorem ipsum dolor sit amet, consetetur sadipscing elitr, sed diam nonumy eirmod.</p>
    <p style="margin-top:32px"><strong>Sehen Sie hier einige unserer Arbeiten.</strong></p>
  </div>

  <div class="abs gallery">
    <div class="tile tile-wide" role="img" aria-label="Foto: historisches Stadtpalais mit Fahnen" style="background:linear-gradient(#b9b3a1,#8f8a7d)"></div>
    <div class="tile" role="img" aria-label="Foto: Altbaufassaden" style="background:linear-gradient(#a9a59c,#7e7c76)"></div>
    <div class="tile" role="img" aria-label="Foto: weiße Wohnhausfassade" style="background:linear-gradient(#c9cdd2,#6e7378)"></div>
    <div class="tile" role="img" aria-label="Foto: Eichentür, vergrößerbar" style="background:#4d5358">
      <svg class="abs" style="left:62px;top:38px" width="28" height="28"><circle cx="14" cy="14" r="12" fill="none" stroke="#fff" stroke-width="1.5"/><line x1="14" y1="8" x2="14" y2="20" stroke="#fff" stroke-width="1.5"/><line x1="8" y1="14" x2="20" y2="14" stroke="#fff" stroke-width="1.5"/></svg>
    </div>
    <div class="tile" role="img" aria-label="Foto: Spachtelarbeiten an einer Wand" style="background:linear-gradient(#a89d93,#6e6058)"></div>
    <div class="tile" role="img" aria-label="Foto: Erker einer Altbaufassade" style="background:linear-gradient(#d3c3a2,#5a5a66)"></div>
    <div class="tile" role="img" aria-label="Foto: Ladenschild an einer Fassade" style="background:linear-gradient(#5d86c2,#2f5aa0)"></div>
    <div class="tile" role="img" aria-label="Foto: Verkaufsraum eines Ladens" style="background:linear-gradient(#857a70,#3f3832)"></div>
    <div class="tile" role="img" aria-label="Foto: moderne Haustür" style="background:linear-gradient(#3d3f41,#202224)"></div>
    <div class="tile" role="img" aria-label="Foto: renovierter Sanitärraum" style="background:linear-gradient(#c2b7a5,#8d7e67)"></div>
    <div class="tile" role="img" aria-label="Foto: Maler bei der Arbeit an der Decke" style="background:linear-gradient(#e2e2e0,#9a9a98)"></div>
    <div class="tile" role="img" aria-label="Foto: weißes Treppenhaus" style="background:linear-gradient(#efefef,#9c9c9c)"></div>
  </div>

  <footer class="abs footer">
    <div class="abs" style="left:145px;top:48px;font-size:19px"><span style="color:var(--orange)">Kolbrit</span> GmbH</div>
    <div class="abs" style="left:373px;top:50px">Lindenhofweg 7<br>82031 Grünau</div>
    <div class="abs" style="left:585px;top:50px">Tel.:&nbsp; +49 89 555010<br>Fax:&nbsp;&nbsp; +49 89 555011</div>
    <div class="abs" style="left:826px;top:50px">Mail:&nbsp; info@kolbrit-gmbh.de</div>
  </footer>
  <div class="abs footbar">
    <div class="abs" style="left:145px;top:10px">© kolbrit 2020</div>
    <div class="abs" style="right:146px;top:10px">Kontakt &nbsp;•&nbsp; Impressum &nbsp;•&nbsp; Datenschutz</div>
  </div>
</div>

<!-- Lightbox view -->
<div class="abs stage"></div>
<div class="abs lightbox">
  <div class="abs" style="left:715px;top:75px;width:240px;height:455px;background:#2b3034"></div>
  <div class="abs" style="left:73px;top:42px;width:922px;height:1px;background:#3e4449"></div>
  <svg class="abs" style="left:1023px;top:18px" width="22" height="22"><line x1="2" y1="2" x2="20" y2="20" stroke="#fff" stroke-width="2"/><line x1="20" y1="2" x2="2" y2="20" stroke="#fff" stroke-width="2"/></svg>
  <div class="abs" role="img" aria-label="Foto: renovierte Eichentür mit Steinportal und Laterne" style="left:347px;top:56px;width:371px;height:516px;background:linear-gradient(#e4e2dc,#d1cdc3 40%,#5a3322 55%,#6e4028 80%,#cfcbc1)"></div>
  <svg class="abs" style="left:24px;top:326px" width="18" height="28"><polyline points="15,2 3,14 15,26" fill="none" stroke="#fff" stroke-width="2"/></svg>
  <svg class="abs" style="left:1026px;top:326px" width="18" height="28"><polyline points="3,2 15,14 3,26" fill="none" stroke="#fff" stroke-width="2"/></svg>
  <div class="abs" style="left:73px;top:590px;width:922px;height:1px;background:#3e4449"></div>
  <div class="abs lb-caption">Renovierung einer stark verwitterten Eichentür im Zuge der kompletten Fassadensanierung<br>mit Graumalerei um Fenster-, Tür- und Abschlusselemente.</div>
  <div class="abs lb-caption" style="left:937px">4 / 16</div>
</div>

</body>
</html>
```